Detail Shop Business card design

i need a business card design for my new detailing company called 'Brisk's Polish Works'. i want an all black and white design . simple, direct and to the point. i want the designer to choose a fitting font to match the logothe front should have logo, address, phone and email and the back side should have a slogan and text indicating that we offer services on anything including cars, trucks, motorcycles and RVs. slogan will read "we take pride in your ride"
maybe also very small on the back side the IG icon with Brisks_Polish_Works

phone 208.417.6352
address 3847 E Larkin Ave
Spokane WA 99214
email: BrisksPolish@mailvexo.com

Target Market(s)

all ages , auto enthusiasts

Industry/Entity Type

Automotive

Contact Information for Business Card

the front should have logo, address, phone and email and the back side should have a slogan and text indicating that we offer services on anything including cars, trucks, motorcycles and RVs. slogan will read "we take pride in your ride"

phone 208.417.6352
address 3847 E Larkin Ave
Spokane WA 99214

Colors
000000
ffffff

Requirements
Must have
• bold font and very simple design with good spacing
Nice to have
• anything creative from the designer indicating we service any types of vehicles
Should not have
• any colors ,

```html
<!DOCTYPE html>
<html lang="en">
<head>
<meta charset="utf-8">
<title>Brisk's Polish Works – Business Card</title>
<link href="https://fonts.googleapis.com/css2?family=Roboto:wght@400;700&family=Roboto+Condensed:wght@700&family=Pathway+Gothic+One&display=swap" rel="stylesheet">
<style>
  :root {
    --ink: #000000;
    --paper: #ffffff;
    --card: #f7f7f7;
    --muted: #555555;
    --backdrop: #e4e4e4;
    --shadow: rgba(0,0,0,0.25);
    --art-dark: #8a8a8a;
    --art-light: #d6d6d6;
  }
  html, body { margin: 0; padding: 0; overflow: hidden; }
  body {
    width: 1200px; height: 960px; position: relative;
    background: var(--backdrop);
    font-family: "Roboto", Arial, sans-serif;
    color: var(--ink);
  }
  .card {
    position: absolute; width: 600px; height: 342px;
    background: var(--card);
    box-shadow: 0 3px 8px var(--shadow);
    overflow: hidden;
  }
  .card--front { left: 314px; top: 113px; }
  .card--back { left: 311px; top: 472px; height: 343px; }

  .brand-lockup {
    position: absolute; left: 70px; top: 70px; width: 220px; height: 170px;
    display: flex; flex-direction: column; align-items: center; justify-content: center; gap: 14px;
  }
  .brand-mark { width: 34px; height: 34px; border-radius: 50%; background: var(--ink); }
  .brand-name {
    font-family: "Roboto Condensed", "Arial Narrow", sans-serif; font-weight: 700;
    font-size: 26px; line-height: 1.05; text-align: center; text-transform: uppercase;
  }
  .divider { position: absolute; left: 308px; top: 72px; width: 1px; height: 160px; background: #bdbdbd; }

  .contact { position: absolute; left: 334px; top: 72px; }
  .contact__name {
    font-family: "Roboto Condensed", "Arial Narrow", sans-serif; font-weight: 700;
    font-size: 21px; margin: 0; line-height: 24px;
  }
  .contact__role { font-size: 14.5px; color: var(--muted); margin: 0 0 16px; letter-spacing: 0.3px; }
  .contact__address { font-size: 14.5px; color: var(--muted); line-height: 19px; margin: 0 0 14px; }
  .contact__list { list-style: none; margin: 0; padding: 0; font-size: 14.5px; color: var(--muted); }
  .contact__list li { display: flex; align-items: center; gap: 9px; height: 19px; }
  .contact__list svg { width: 13px; height: 13px; fill: var(--ink); flex: none; }

  .web-band {
    position: absolute; left: 0; top: 294px; width: 566px; height: 33px;
    background: var(--ink); color: var(--paper);
    display: flex; align-items: center; justify-content: center;
    font-size: 14.5px; letter-spacing: 4.2px; padding-left: 40px; box-sizing: border-box;
  }
  .web-badge {
    position: absolute; left: 536px; top: 283px; width: 52px; height: 52px;
    border-radius: 50%; background: var(--ink); border: 3px solid var(--paper);
    box-shadow: 0 0 0 1px var(--ink);
  }

  .vehicle-art {
    position: absolute; left: 126px; top: 92px; width: 356px; height: 118px;
    background: radial-gradient(ellipse at 50% 45%, var(--art-dark) 0%, var(--art-light) 75%, var(--card) 100%);
    border-radius: 50% 50% 12px 12px / 60% 60% 12px 12px;
  }
  .vehicle-ground {
    position: absolute; left: 114px; top: 214px; width: 380px; height: 10px;
    background: radial-gradient(ellipse at 50% 0%, var(--art-dark) 0%, transparent 70%);
  }
  .slogan {
    position: absolute; left: 0; width: 100%; top: 271px; text-align: center;
    font-family: "Roboto", Arial, sans-serif; font-weight: 700; font-size: 17px; margin: 0;
  }
  .slogan-rule { position: absolute; left: 137px; top: 294px; width: 325px; height: 2px; background: var(--ink); }
  .services {
    position: absolute; left: 0; width: 100%; top: 297px; text-align: center;
    font-family: "Pathway Gothic One", "Arial Narrow", sans-serif; font-size: 16px; margin: 0;
  }
</style>
</head>
<body>
  <section class="card card--front">
    <div class="brand-lockup">
      <span class="brand-mark"></span>
      <span class="brand-name">Brisk's<br>Polish Works</span>
    </div>
    <div class="divider"></div>
    <div class="contact">
      <h1 class="contact__name">DANA WHITLOW</h1>
      <p class="contact__role">CEO/FOUNDER</p>
      <p class="contact__address">3847 E Larkin Ave<br>Spokane WA 99214</p>
      <ul class="contact__list">
        <li><svg viewBox="0 0 24 24"><path d="M6.6 10.8a15.1 15.1 0 0 0 6.6 6.6l2.2-2.2a1 1 0 0 1 1-.25 11.4 11.4 0 0 0 3.6.57 1 1 0 0 1 1 1V20a1 1 0 0 1-1 1A17 17 0 0 1 3 4a1 1 0 0 1 1-1h3.5a1 1 0 0 1 1 1c0 1.25.2 2.450.57 3.6a1 1 0 0 1-.25 1z"/></svg>208.417.6352</li>
        <li><svg viewBox="0 0 24 24"><path d="M7 1h10a2 2 0 0 1 2 2v18a2 2 0 0 1-2 2H7a2 2 0 0 1-2-2V3a2 2 0 0 1 2-2zm0 3v14h10V4zm5 15.5a1 1 0 1 0 0 2 1 1 0 0 0 0-2z"/></svg>208 563 4471</li>
        <li><svg viewBox="0 0 24 24"><path d="M2 5h20v14H2zm2 2v.5l8 5 8-5V7l-8 5z"/></svg>BrisksPolish@mailvexo.com</li>
      </ul>
    </div>
    <div class="web-band">www.briskspolish.com</div>
    <div class="web-badge"></div>
  </section>

  <section class="card card--back">
    <div class="vehicle-art" role="img" aria-label="Black and white illustration of a classic hot rod car"></div>
    <div class="vehicle-ground"></div>
    <h2 class="slogan">WE TAKE PRIDE IN YOUR RIDE</h2>
    <div class="slogan-rule"></div>
    <p class="services">we offer services on anything including cars, trucks, motorcycles &amp; RVS</p>
  </section>
</body>
</html>
```